Varentoria Business Card and Letter Head

We are a leadership assessment consultancy based in Sydney, Australia. We help executive-level decison-makers select leaders for more senior level roles in corporate and government organisations. Our methodology is based on the latest research from the field of neuroscience.
We need a business card design and matching letter head that presents our company, Varentoria, as a:
1. trusted adviser to senior executive-level decison makers
2. niche consultancy who are experts in the field of assessing leadership talent
3. results-focused solution provider who balance scientific methods with pragmatic solutions
The following company details should be used in all designs:
Company Name: Varentoria
Details (for business card):
Derek Hanford
Prime Capacity Officer
Level 18, Marlow Tower
7 Marlow Square
Harwick, NSW 2417 Australia
Phone: 1300 582 714
Mobile: 0412 637 258
Email: derek.hanford@varentoria-example.com.au
Website: varentoria-example.com.au
I have attached the logo for Varentoria (for both a white and black background) - your business card and letter head designs must incoporate this logo and colour scheme.
Thanks for your interest in this project, I'm looking forward to receiving your ideas.
Regards,
Derek
Target Market(s)
Executive-level decison-makers in corporate and government organisations (e.g., CEO, VP, Head of Human Resources)
Industry/Entity Type
Leadership
Look and feel

```html
<!DOCTYPE html>
<html lang="en">
<head>
<meta charset="utf-8">
<title>Varentoria Business Card</title>
<link rel="stylesheet" href="https://fonts.googleapis.com/css2?family=Source+Sans+3:wght@300;400;600;700&display=swap">
<style>
  :root {
    --backdrop: #e9e7e4;
    --card: #ffffff;
    --ink: #3a3a3e;
    --ink-soft: #4a4a4e;
    --accent: #c0281d;
    --muted: #6b6b70;
  }
  * { box-sizing: border-box; margin: 0; padding: 0; }
  html, body { width: 1200px; height: 427px; overflow: hidden; }
  body {
    position: relative;
    background: var(--backdrop);
    font-family: "Source Sans 3", "Helvetica Neue", Arial, sans-serif;
    color: var(--ink);
  }
  .card {
    position: absolute;
    top: 67px;
    width: 520px;
    height: 295px;
    background: var(--card);
    border-radius: 22px;
    overflow: hidden;
    box-shadow: 0 4px 14px rgba(0,0,0,0.18);
  }
  .card--front { left: 57px; }
  .card--back { left: 608px; }

  /* Front */
  .brand {
    position: absolute;
    left: 62px;
    top: 26px;
    display: flex;
    align-items: center;
    gap: 22px;
  }
  .brand__square {
    width: 58px; height: 58px;
    background: var(--accent);
  }
  .brand__name {
    font-size: 50px;
    font-weight: 600;
    line-height: 1;
    color: var(--ink);
    letter-spacing: -0.5px;
  }
  .tagline {
    position: absolute;
    left: 165px;
    top: 88px;
    font-size: 17px;
    font-weight: 300;
    letter-spacing: 0.8px;
    color: var(--muted);
  }
  .person {
    position: absolute;
    left: 0; right: 0;
    top: 140px;
    text-align: center;
    padding-left: 10px;
  }
  .person__name {
    font-size: 19px;
    font-weight: 400;
    color: var(--accent);
    letter-spacing: 0.3px;
  }
  .person__title {
    font-size: 13px;
    color: var(--ink-soft);
    margin-top: 2px;
  }
  .contacts {
    position: absolute;
    left: 23px;
    top: 205px;
    font-size: 12px;
    line-height: 16.5px;
    color: var(--ink-soft);
    list-style: none;
  }
  .contacts__label { color: var(--accent); }
  .address {
    position: absolute;
    left: 290px;
    top: 224px;
    font-size: 12px;
    line-height: 16.5px;
    color: var(--ink-soft);
    font-style: normal;
  }
  .website {
    position: absolute;
    left: 23px;
    top: 265px;
    font-size: 12px;
    font-weight: 700;
    letter-spacing: 0.4px;
    color: var(--ink);
  }
  .accent-band {
    position: absolute;
    left: 295px;
    right: 0;
    top: 270px;
    height: 21px;
    background: var(--accent);
  }

  /* Back */
  .back-brand {
    position: absolute;
    left: 0; right: 0;
    top: 108px;
    display: flex;
    flex-direction: column;
    align-items: center;
    gap: 14px;
    padding-left: 80px;
  }
  .back-brand__square {
    width: 40px; height: 40px;
    background: var(--accent);
  }
  .back-brand__name {
    font-size: 40px;
    font-weight: 600;
    color: var(--ink);
    line-height: 1;
  }
  .back-url {
    position: absolute;
    left: 0; right: 0;
    top: 228px;
    padding-left: 80px;
    text-align: center;
    font-size: 12.5px;
    letter-spacing: 1.6px;
    color: var(--ink-soft);
    text-transform: uppercase;
  }
</style>
</head>
<body>
  <section class="card card--front" aria-label="Business card front">
    <div class="brand">
      <span class="brand__square" aria-hidden="true"></span>
      <span class="brand__name">Varentoria</span>
    </div>
    <p class="tagline">ASSESSING EXECUTIVE CAPACITY</p>

    <div class="person">
      <p class="person__name">DEREK HANFORD</p>
      <p class="person__title">Prime Capacity Officer</p>
    </div>

    <ul class="contacts">
      <li><span class="contacts__label">P:</span> 1300 582 714</li>
      <li><span class="contacts__label">M:</span> 0412 637 258</li>
      <li><span class="contacts__label">E:</span> derek.hanford@varentoria-example.com.au</li>
    </ul>

    <address class="address">
      Level 18, Marlow Tower, 7 Marlow Square,<br>
      Harwick, NSW 2417 Australia
    </address>

    <p class="website">www.VARENTORIA-EXAMPLE.com.au</p>

    <div class="accent-band" aria-hidden="true"></div>
  </section>

  <section class="card card--back" aria-label="Business card back">
    <div class="back-brand">
      <span class="back-brand__square" aria-hidden="true"></span>
      <span class="back-brand__name">Varentoria</span>
    </div>
    <p class="back-url">varentoria-example.com.au</p>
  </section>
</body>
</html>
```